Collectibles expert needs a new business card design.

My current business card makes me look to high end. It may even make me look arrogant or too stuffy. I do work with high end clients and their items but most of my business is with average people with average items. My business name is Walter Brennick's Old Orchard Salvage Co. The idea was that I mine the streets helping people discover the treasures buried in their homes. That could be art, jewelry, coins, etc. The name and an older logo I used does not make immediate sense to most people. I tried to go with just my picture and name and that is the current card I am changing. I help people who need to downsize. Whether they are getting rid of one item, a collection or a house full of items I help them discover what they have, what it is worth and what are the best ways we can get the most for them. This may be a combination of estate sale (which I dont do) auction or sell directly to a dealer or collector. Usually it is a combination of these. My main goal is to help make sure they dont accidently sell a Picasso painting in a garage sale. I am uploading a copy of my old card and the old logo I used to use but the winning card design will need to be much different than these. You can learn a little more about me at www.walterjbrennick.example, www.oldorchardsalv.example and www.facebook.com/oosalco. I hope someone can look at what I do and come up with a very unique design that will be equally effective if my client is high income or if my client is low to mid income. I do not care if it is a one or two sided card as long as it conveys my contact information and a good representation of what I do.

Target Market(s)

People who are getting rid of items. These can be elderly couples or individuals that are moving to an active living community and will have less space so they need to sell items. This can also include the children of elder parents that dont want their stuff and want to find solutions to help them get rid of their items.

Contact Information for Business Card

The card should have my business name Walter Brennick's Old Orchard Salvage Co., phone number 555-302-71938, email walter@oldorchardsalvage.example and website www.oldorchardsalvage.example. Would also like to include Buyer, Broker, Consultant and Appraiser. We can put Walter J. Brennick, ISA on the opposite side of the company name since it includes my name as well.

Font styles to use
Sans Serif

Colors

Designer to choose colors to be used in the design.

Requirements
Must have
• My project must have a professional look. It must not alienate low income clients and should still be appealing to high value clients.

```html
<!DOCTYPE html>
<html lang="en">
<head>
<meta charset="utf-8">
<title>Old Orchard Salvage Co. — Business Card</title>
<link rel="stylesheet" href="https://fonts.googleapis.com/css2?family=Oswald:wght@700&family=Lato:wght@400&display=swap">
<style>
  :root {
    --backdrop: #e4e5e7;
    --paper: #ffffff;
    --navy: #1f3d5c;
    --navy-text: #1e3a5f;
    --rule: rgba(255, 255, 255, 0.45);
    --ink-light: #ffffff;
    --mark-grey: #6f6f6f;
  }
  * { box-sizing: border-box; margin: 0; padding: 0; }
  html, body {
    width: 1200px;
    height: 782px;
    overflow: hidden;
    background: var(--backdrop);
  }
  .sheet {
    width: 1200px;
    height: 782px;
    display: flex;
    align-items: center;
    justify-content: center;
    gap: 48px;
  }
  .card {
    width: 540px;
    height: 309px;
    border-radius: 2px;
    box-shadow: 0 6px 18px rgba(0, 0, 0, 0.18);
    display: flex;
    flex-direction: column;
    align-items: center;
    justify-content: center;
    text-align: center;
  }
  .card--front { background: var(--paper); }
  .card--back { background: var(--navy); color: var(--ink-light); }

  .brand { display: flex; flex-direction: column; align-items: center; gap: 14px; }
  .brand__dot {
    width: 62px;
    height: 62px;
    border: 4px solid var(--mark-grey);
    border-radius: 50%;
  }
  .brand__name {
    font-family: "Oswald", sans-serif;
    font-weight: 700;
    color: var(--navy-text);
    text-transform: uppercase;
    font-size: 22px;
    line-height: 1.15;
    letter-spacing: 0.2px;
  }

  .contact__name {
    font-family: "Oswald", sans-serif;
    font-weight: 700;
    font-size: 19px;
    text-transform: uppercase;
    letter-spacing: 0.3px;
  }
  .contact__role {
    font-family: "Lato", sans-serif;
    font-size: 15px;
    margin-top: 2px;
  }
  .contact__rule {
    width: 190px;
    height: 1px;
    background: var(--rule);
    margin: 14px auto 12px;
  }
  .contact__line {
    font-family: "Lato", sans-serif;
    font-size: 15px;
    line-height: 1.35;
  }
</style>
</head>
<body>
  <main class="sheet">
    <section class="card card--front" aria-label="Card front">
      <div class="brand">
        <span class="brand__dot" aria-hidden="true"></span>
        <p class="brand__name">Walter Brennick's<br>Old Orchard Salvage Co.,</p>
      </div>
    </section>

    <section class="card card--back" aria-label="Card back">
      <h1 class="contact__name">Walter J. Brennick, ISA</h1>
      <p class="contact__role">Buyer, Broker, Consultant and Appraiser</p>
      <div class="contact__rule"></div>
      <p class="contact__line">P: 555-302-71938</p>
      <p class="contact__line">E: walter@oldorchardsalvage.example</p>
      <p class="contact__line">www.oldorchardsalvage.example</p>
    </section>
  </main>
</body>
</html>
```